Retail Package for Ammunition Company

We are looking for a packaging design for a retail boxed ammunition. The "look". Attached will be the logo to be used. The logo is attached and a can be manipulated on the box. Box to represent strength and accuracy. Will need to provide .psd files to allow in house personnel to add/remove text to other calibers and warnings. Wow me with your designs!

Browse Other Brands: http://www.brightfalconsupply.com/brands

The packaging needs to include:
Logo- provided and the following text:

FRONT 1. 9mm 115gr FMJ

BACK 2. WARNING: To avoid serious injury: (1) use only ammunition in good condition; use only in modern firearms in good condition marked for .22 Long Rifle (LR) cartridges; (2) always be sure barrel is free of any obstructions; the barrel should be checked in case of light recoil, or an unusually loud or weak sound heard during firing; (3) wear eye and ear protection; (4) if gun fails to fire, avoid exposure to breech when unloading and point muzzle in a safe direction. Keep firearm pointed in safe direction at all times; (5) discharge may occur if rim is struck; handle with caution, do not drop. (6) Do not shoot at hard surfaces or water to prevent ricochet; (7) Bullet is capable of traveling extreme distances. Know your backstop; (8) Store in cool dry place

3. LEAD WARNING: Discharging firearms in poorly ventilated areas, cleaning firearms, or handling ammunition may result in exposure to lead and other substances known to cause birth defects, reproductive harm, and other serious physical injury. Have adequate ventilation at all times. Wash hands thoroughly after exposure.

Dimensions ; (LxWxH): 5.25" x 2.625" x 1.125"

Target Market(s)

Ammunition Industry

```html
<!DOCTYPE html>
<html lang="en">
<head>
<meta charset="utf-8">
<title>Ironwing Armory – 9mm 115gr FMJ Retail Box</title>
<link rel="stylesheet" href="https://fonts.googleapis.com/css2?family=Oswald:wght@700&family=Montserrat:wght@400;700&display=swap">
<style>
  :root {
    --stage: #f3f3f3;
    --red-deep: #5a1418;
    --red-mid: #8e1a1c;
    --red-bright: #9a1b1c;
    --red-band: #6e0d10;
    --brand-red: #8a1418;
    --paper: #ffffff;
    --ink-light: #ffffff;
  }
  * { box-sizing: border-box; margin: 0; padding: 0; }
  html, body {
    width: 1200px; height: 750px; overflow: hidden;
    background: var(--stage);
    font-family: "Montserrat", Arial, sans-serif;
  }
  .packaging {
    position: absolute; left: 59px; top: 52px;
    display: grid;
    grid-template-columns: 188px 880px;
    grid-template-rows: 188px 440px;
    column-gap: 14px; row-gap: 12px;
  }

  /* Top panel */
  .top-panel {
    grid-column: 2; grid-row: 1;
    position: relative;
    background: var(--paper);
    overflow: hidden;
  }
  .top-panel .top-band { position: absolute; inset: 0; width: 100%; height: 100%; }
  .top-brand {
    position: absolute; left: 0; right: 0; top: 22px;
    font-family: "Oswald", Arial, sans-serif; font-weight: 700;
    color: var(--brand-red); text-align: center;
  }
  .top-brand .brand-word { display: block; font-size: 44px; line-height: 1; letter-spacing: 2px; }
  .top-brand .brand-sub {
    display: flex; align-items: center; justify-content: center; gap: 12px;
    font-size: 14px; letter-spacing: 7px; margin-top: 5px;
  }
  .top-brand .brand-sub::before,
  .top-brand .brand-sub::after { content: ""; width: 70px; height: 2px; background: var(--brand-red); }
  .top-descriptor {
    position: absolute; left: 0; right: 0; bottom: 14px;
    color: var(--ink-light); text-align: center;
    font-weight: 700; font-size: 13px; letter-spacing: 2px; line-height: 1.45;
    text-transform: uppercase;
  }

  /* End panel */
  .end-panel {
    grid-column: 1; grid-row: 2;
    background: linear-gradient(160deg, var(--red-deep) 0%, var(--red-mid) 45%, var(--red-deep) 100%);
    color: var(--ink-light);
    display: flex; flex-direction: column; align-items: center; justify-content: space-between;
    padding: 54px 12px 38px;
    text-align: center;
  }
  .end-brand {
    font-family: "Oswald", Arial, sans-serif; font-weight: 700;
    letter-spacing: 2px; line-height: 1.1;
  }
  .end-brand .brand-word { display: block; font-size: 28px; }
  .end-brand .brand-sub { display: block; font-size: 14px; letter-spacing: 6px; }
  .end-spec .caliber {
    font-weight: 700; font-size: 27px; white-space: nowrap; line-height: 1.15;
  }
  .end-spec .descriptor {
    margin-top: 6px;
    font-size: 11px; font-weight: 700; text-transform: uppercase; letter-spacing: 1px; line-height: 1.5;
  }

  /* Back panel */
  .back-panel {
    grid-column: 2; grid-row: 2;
    position: relative;
    background: linear-gradient(100deg, var(--red-deep) 0%, var(--red-bright) 55%, var(--red-deep) 100%);
    overflow: hidden;
  }
  .back-panel .cap-shape { position: absolute; inset: 0; width: 100%; height: 100%; }
  .brand-lockup {
    position: absolute; left: 380px; width: 420px; top: 36px;
    font-family: "Oswald", Arial, sans-serif; font-weight: 700;
    color: var(--brand-red); text-align: center;
  }
  .brand-lockup .brand-word { display: block; font-size: 54px; line-height: 1; letter-spacing: 2px; }
  .brand-lockup .brand-sub {
    display: flex; align-items: center; justify-content: center; gap: 12px;
    font-size: 17px; letter-spacing: 8px; margin-top: 6px;
  }
  .brand-lockup .brand-sub::before,
  .brand-lockup .brand-sub::after { content: ""; width: 80px; height: 2px; background: var(--brand-red); }
  .warnings {
    position: absolute; left: 40px; right: 40px; top: 202px;
    color: var(--ink-light);
    font-size: 12.5px; line-height: 1.42;
  }
  .warnings p + p { margin-top: 12px; }
  .warnings .label { font-weight: 700; font-size: 16px; letter-spacing: 0.5px; }
</style>
</head>
<body>
  <main class="packaging">
    <section class="top-panel" aria-label="Top panel">
      <svg class="top-band" viewBox="0 0 880 188" preserveAspectRatio="none" aria-hidden="true">
        <defs>
          <linearGradient id="bandShade" x1="0" x2="1" y1="0" y2="0">
            <stop offset="0" stop-color="#8a1013"/>
            <stop offset="1" stop-color="#6a0a0d"/>
          </linearGradient>
        </defs>
        <polygon points="0,188 0,150 880,118 880,188" fill="url(#bandShade)"/>
      </svg>
      <div class="top-brand">
        <span class="brand-word">IRONWING</span>
        <span class="brand-sub">ARMORY</span>
      </div>
      <div class="top-descriptor">Full Metal Jacket<br>FMJ | Elite Ammunition</div>
    </section>

    <section class="end-panel" aria-label="End panel">
      <div class="end-brand">
        <span class="brand-word">IRONWING</span>
        <span class="brand-sub">ARMORY</span>
      </div>
      <div class="end-spec">
        <div class="caliber">9mm 115gr</div>
        <div class="descriptor">Full Metal Jacket<br>FMJ / Elite Ammunition</div>
      </div>
    </section>

    <section class="back-panel" aria-label="Back panel">
      <svg class="cap-shape" viewBox="0 0 880 440" preserveAspectRatio="none" aria-hidden="true">
        <rect x="0" y="0" width="880" height="20" fill="#6e0d10"/>
        <polygon points="0,20 880,20 880,44 560,134 30,186" fill="#ffffff"/>
      </svg>
      <div class="brand-lockup">
        <span class="brand-word">IRONWING</span>
        <span class="brand-sub">ARMORY</span>
      </div>
      <div class="warnings">
        <p><span class="label">LEAD WARNING:</span> Discharging firearms in poorly ventilated areas, cleaning firearms, or handling ammunition may result in exposure to lead and other substances known to cause birth defects, reproductive harm, and other serious physical injury. Have adequate ventilation at all times. Wash hands thoroughly after exposure.</p>
        <p><span class="label">WARNING:</span> To avoid serious injury: (1) use only ammunition in good condition; use only in modern firearms in good condition marked for .22 Long Rifle (LR) cartridges; (2) always be sure barrel is free of any obstructions; the barrel should be checked in case of light recoil, or an unusually loud or weak sound heard during firing; (3) wear eye and ear protection; (4) if gun fails to fire, avoid exposure to breech when unloading and point muzzle in a safe direction. Keep firearm pointed in safe direction at all times; (5) discharge may occur if rim is struck; handle with caution, do not drop. (6) Do not shoot at hard surfaces or water to prevent ricochet; (7) Bullet is capable of traveling extreme distances. Know your backstop; (8) Store in cool dry place</p>
      </div>
    </section>
  </main>
</body>
</html>
```